Salon and Spa Distributor Business Card

Need a business card. We are are distributor in the salon and spa industry. We identify with natural beauty. Need a card with:
Company Name: Petal Quarry"
Title: "President & CEO"
Address
Company Phone number
email
website
Tag Line:" The Professional Salon Source"

Industry/Entity Type

Business

Contact Information for Business Card

Name: Dov Strommen
Title: "President & CEO"
Address: 31 Harlow Ln, Bexmoor, NJ 07813
Company Phone number: 800-463-5918
email: dovstrommen@petalquarry.example
website: www.petalquarry.example

Requirements
Should not have
• No black backgrounds

```html
<!DOCTYPE html>
<html lang="en">
<head>
<meta charset="utf-8">
<title>Petal Quarry — Business Card</title>
<link rel="stylesheet" href="https://fonts.googleapis.com/css2?family=Questrial&display=swap">
<style>
  :root {
    --backdrop: #d8d1c6;
    --green-deep: #17662a;
    --green-mid: #2a8038;
    --green-art-dark: #1d6f2c;
    --green-art-light: #4c9c55;
    --frost: #eef1ee;
    --frost-shade: #dfe6e0;
    --text-light: #eef3ee;
    --text-muted: #dce8dd;
    --icon-box: #cfd9cf;
    --icon-ink: #3a7c45;
  }
  * { margin: 0; padding: 0; box-sizing: border-box; }
  html, body {
    width: 1200px; height: 970px; overflow: hidden;
    background: var(--backdrop);
    font-family: "Questrial", "Century Gothic", sans-serif;
  }
  .business-card {
    position: absolute; left: 80px; top: 190px;
    width: 1040px; height: 590px;
    overflow: hidden;
    background: linear-gradient(90deg,
      var(--green-deep) 0%, var(--green-mid) 50%,
      var(--frost-shade) 66%, var(--frost) 100%);
    box-shadow: 0 10px 30px rgba(0,0,0,0.18);
    color: var(--text-light);
  }
  .illustration-area {
    position: absolute; left: 575px; top: 0;
    width: 465px; height: 590px;
    border-radius: 60% 0 0 45% / 50% 0 0 50%;
    background: linear-gradient(160deg, var(--green-art-light) 0%, var(--green-art-dark) 55%, var(--green-art-light) 100%);
  }
  .brand-name {
    position: absolute; left: 60px; top: 50px;
    font-size: 62px; font-weight: 400; letter-spacing: 0.5px;
    color: var(--text-light); line-height: 1;
  }
  .tagline {
    position: absolute; left: 60px; top: 120px;
    font-size: 26px; letter-spacing: 1.6px; color: var(--text-muted);
  }
  .person-name {
    position: absolute; left: 60px; top: 240px;
    font-size: 34px; letter-spacing: 0.5px;
  }
  .person-title {
    position: absolute; left: 60px; top: 278px;
    font-size: 26px; color: var(--text-muted);
  }
  .address {
    position: absolute; left: 60px; top: 356px;
    font-size: 26px; line-height: 34px; color: var(--text-muted); font-style: normal;
  }
  .contact-list {
    position: absolute; left: 60px; top: 444px;
    list-style: none; font-size: 26px; color: var(--text-muted);
  }
  .contact-item { display: flex; align-items: center; height: 34px; white-space: nowrap; }
  .contact-icon {
    width: 28px; height: 28px; margin-right: 14px;
    background: var(--icon-box);
    display: flex; align-items: center; justify-content: center;
  }
  .contact-icon svg { width: 20px; height: 20px; }
</style>
</head>
<body>
  <div class="business-card">
    <div class="illustration-area" role="img" aria-label="Green illustration of a woman's profile with flowing leafy hair and floating leaves, symbolising natural beauty"></div>

    <div class="brand-name">Petal Quarry</div>
    <div class="tagline">The Professional Salon Source</div>

    <div class="person-name">Dov Strommen</div>
    <div class="person-title">President &amp; CEO</div>

    <address class="address">31 Harlow Ln,<br>Bexmoor, NJ 07813</address>

    <ul class="contact-list">
      <li class="contact-item">
        <span class="contact-icon">
          <svg viewBox="0 0 20 20"><path d="M3 7c0-2 3-3 7-3s7 1 7 3v1h-4V7H7v1H3z M5 10h10l1 6H4z" fill="var(--icon-ink)"/></svg>
        </span>800-463-5918
      </li>
      <li class="contact-item">
        <span class="contact-icon">
          <svg viewBox="0 0 20 20"><rect x="2" y="5" width="16" height="11" fill="none" stroke="var(--icon-ink)" stroke-width="1.6"/><path d="M2 5l8 6 8-6" fill="none" stroke="var(--icon-ink)" stroke-width="1.6"/></svg>
        </span>dovstrommen@petalquarry.example
      </li>
      <li class="contact-item">
        <span class="contact-icon">
          <svg viewBox="0 0 20 20"><circle cx="10" cy="10" r="7.5" fill="none" stroke="var(--icon-ink)" stroke-width="1.5"/><ellipse cx="10" cy="10" rx="3.2" ry="7.5" fill="none" stroke="var(--icon-ink)" stroke-width="1.3"/><path d="M2.5 10h15M4 6h12M4 14h12" stroke="var(--icon-ink)" stroke-width="1.2"/></svg>
        </span>www.petalquarry.example
      </li>
    </ul>
  </div>
</body>
</html>
```